New web design for a service provider in the medical field

We are looking for a new design for our website. We are a company that repairs and sells medical endoscopes. Our customers include doctors and hospitals. Our current website can be found at https://lumavex.de/en/lumavex-english.
We need a new web design (without programming) for the following 3 pages:
-Startpage https://lumavex.de/en/lumavex-english/
-Used endoscopes https://lumavex.de/en/used-endoscopes/
-Purchase https://lumavex.de/en/purchase/
The design should be modern and stylish.
The blue color of the logo should be reflected on the page, but not too intrusive.
I have uploaded the images from the header. If more images are needed, let me know and I will upload them.

Target Market(s)
Doctors and hospitals

```html
<!DOCTYPE html>
<html lang="en">
<head>
<meta charset="utf-8">
<title>Lumavex – Purchase</title>
<link href="https://fonts.googleapis.com/css2?family=Outfit:wght@300;400;500;600;700;800&family=Barlow:ital,wght@0,400;0,500;0,600;1,400&display=swap" rel="stylesheet">
<style>
:root{
  --blue:#23a3dd;
  --navy:#16334d;
  --navy-deep:#12293f;
  --ink:#1f3246;
  --text:#3c4a58;
  --line:#b9c6d2;
  --pale:#eef3f7;
  --white:#ffffff;
}
*{box-sizing:border-box;margin:0;padding:0}
html,body{width:1200px;height:3423px;overflow:hidden}
body{position:relative;background:var(--white);font-family:"Outfit",sans-serif;color:var(--text)}
.abs{position:absolute}
/* header */
.topbar{left:670px;top:0;width:530px;height:47px;background:var(--blue);clip-path:polygon(0 0,100% 0,100% 100%,26px 100%);color:#fff;font:600 12px "Outfit",sans-serif;display:flex;align-items:center;gap:24px;padding-left:40px}
.topbar span{display:flex;align-items:center;gap:7px}
.topbar .ic{width:20px;height:20px;border-radius:50%;background:#fff;display:inline-flex;align-items:center;justify-content:center}
.brand{left:108px;top:48px;font:700 23px "Outfit",sans-serif;color:var(--navy);letter-spacing:.3px;display:flex;align-items:center;gap:8px}
.brand i{width:12px;height:12px;border-radius:50%;background:var(--blue);display:block}
.nav{left:305px;top:74px;display:flex;gap:28px;font:600 12.5px "Outfit",sans-serif;color:var(--navy);letter-spacing:.2px}
.nav a{color:inherit;text-decoration:none;position:relative}
.nav a.active::after{content:"";position:absolute;left:0;right:0;bottom:-9px;height:2px;background:var(--blue)}
.nav .purchase{margin-left:14px}
/* hero */
.hero{left:0;top:117px;width:1200px;height:548px;background:linear-gradient(100deg,#eef2f6 0%,#e4ebf1 45%,#cfd6de 100%)}
.hero-photo{left:440px;top:160px;width:760px;height:420px;background:radial-gradient(ellipse at 55% 50%,#3a3f46 0%,#7d8590 35%,rgba(220,226,232,0) 70%)}
.hero .kicker{position:absolute;left:103px;top:163px;font:400 26px "Outfit",sans-serif;color:var(--blue)}
.hero h1{position:absolute;left:103px;top:195px;font:700 41px/45px "Outfit",sans-serif;color:var(--ink);letter-spacing:.3px}
.band{left:0;width:1200px;height:100px}
.circle-arrow{width:76px;height:76px;border-radius:50%;background:#fff;border:2px solid var(--blue);display:flex;align-items:center;justify-content:center}
/* intro */
.intro-title{left:0;top:722px;width:1200px;text-align:center;font:700 36px/45px "Outfit",sans-serif;color:var(--ink)}
.intro-title span{color:var(--blue)}
.rule{height:3px;width:34px;background:var(--blue)}
.intro-text{left:578px;top:912px;width:505px;font:400 16.5px/27px "Outfit",sans-serif;color:var(--text)}
.intro-text p+p{margin-top:12px}
/* dark cta */
.cta{left:0;top:1338px;width:1200px;height:510px;background:linear-gradient(90deg,#15314b,#1e4666 50%,#173652);}
.cta h2{position:absolute;left:0;top:92px;width:1200px;text-align:center;font:700 32px/36px "Outfit",sans-serif;color:#fff}
.cta p{position:absolute;left:230px;top:200px;width:740px;text-align:center;font:400 17px/22px "Outfit",sans-serif;color:#e3ecf3}
.cta .btn{position:absolute;left:400px;top:277px;width:410px;height:52px;border-radius:26px;background:var(--blue);color:#fff;font:600 16px "Outfit",sans-serif;display:flex;align-items:center;justify-content:center}
/* form */
.form-bg{left:0;top:1848px;width:1200px;height:1140px;background:var(--pale)}
.sec-h{font:600 21px "Outfit",sans-serif;color:var(--ink);letter-spacing:.3px}
.sec-h::after{content:"";display:block;width:70px;height:2px;background:var(--blue);margin-top:10px}
.lbl{font:500 14.5px "Barlow",sans-serif;color:var(--ink)}
.field{background:#fff;border:1px solid var(--line);font:400 15px "Barlow",sans-serif;color:#4c5a68;display:flex;align-items:center;padding:0 19px;justify-content:space-between}
.field.top{align-items:flex-start;padding-top:14px}
.note{font:italic 400 11.5px/19px "Barlow",sans-serif;color:#4c5a68}
.consent{left:170px;top:2812px;width:900px;font:400 11.5px/19px "Barlow",sans-serif;color:#3c4a58}
.check{left:134px;top:2815px;width:22px;height:22px;border:1px solid var(--line);background:#fff}
.send{left:128px;top:2873px;width:162px;height:49px;border-radius:25px;background:var(--blue);color:#fff;font:700 18px "Outfit",sans-serif;display:flex;align-items:center;justify-content:center;letter-spacing:.5px}
.browse{border:1.5px solid var(--blue);border-radius:16px;height:32px;padding:0 18px;display:flex;align-items:center;gap:6px;color:var(--navy);font:600 13px "Barlow",sans-serif}
/* footer */
.footer{left:0;top:3090px;width:1200px;height:333px;background:#fff}
.f-brand{left:134px;top:3150px;font:700 23px "Outfit",sans-serif;color:var(--navy);display:flex;align-items:center;gap:8px}
.f-brand i{width:12px;height:12px;border-radius:50%;background:var(--blue);display:block}
.f-about{left:126px;top:3228px;width:270px;font:400 13px/15px "Outfit",sans-serif;color:#5a6775}
.f-col{top:3130px;border-left:3px solid var(--blue);padding-left:16px;height:22px}
.f-col h4{font:600 15px "Outfit",sans-serif;color:var(--ink);letter-spacing:.3px}
.f-links{font:400 14.5px/29px "Outfit",sans-serif;color:#3c4a58}
.vsep{width:1px;background:#e2e8ee;top:3100px;height:190px}
.social{left:934px;top:3177px;display:flex;gap:6px}
.social span{width:29px;height:29px;border-radius:50%;background:var(--navy)}
.f-rule{left:0;top:3360px;width:1200px;height:1px;background:#dfe5ea}
.copy{left:0;top:3381px;width:1200px;text-align:center;font:400 12.5px "Outfit",sans-serif;color:#6a7683}
</style>
</head>
<body>

<header>
  <div class="abs topbar">
    <span><i class="ic"><svg width="11" height="9" viewBox="0 0 11 9"><rect x=".5" y=".5" width="10" height="8" fill="none" stroke="#23a3dd"/><path d="M.5 .5 5.5 5 10.5 .5" fill="none" stroke="#23a3dd"/></svg></i>info@lumavex.de</span>
    <span><i class="ic"><svg width="11" height="11" viewBox="0 0 12 12"><path d="M2 1l2 0 1 3-1.5 1a7 7 0 003.5 3.5l1-1.5 3 1v2a1 1 0 01-1 1A10 10 0 011 2a1 1 0 011-1z" fill="#23a3dd"/></svg></i>+49 4000 555 120-0</span>
    <span>ENG <svg width="9" height="6" viewBox="0 0 9 6"><path d="M1 1l3.5 3.5L8 1" fill="none" stroke="#fff" stroke-width="1.5"/></svg></span>
  </div>
  <div class="abs brand"><i></i>Lumavex</div>
  <nav class="abs nav">
    <a class="active">ENDOSCOPE REPAIR</a>
    <a>ENDOSCOPY SYSTEMS</a>
    <a>ENDOSCOPY ACCESSORIES ⌄</a>
    <a>ACCESSORIES CATALOG</a>
    <a class="purchase">PURCHASE</a>
  </nav>
</header>

<section class="abs hero">
  <div class="kicker">PURCHASE ENDOSCOPES</div>
  <h1>SUSTAINABLE AND<br>ECONOMICAL</h1>
</section>
<div class="abs hero-photo" role="img" aria-label="Photo of a flexible endoscope control body and insertion tube on a light surface"></div>

<svg class="abs band" style="top:565px" viewBox="0 0 1200 100" preserveAspectRatio="none">
  <polygon points="0,100 1200,100 1200,90 600,55 0,100" fill="#fff"/>
  <polygon points="0,0 600,55 0,100" fill="#23a3dd"/>
  <polygon points="1200,0 600,55 1200,90" fill="#16334d"/>
</svg>
<div class="abs circle-arrow" style="left:565px;top:584px"><svg width="22" height="26" viewBox="0 0 22 26"><path d="M11 2v21M3 15l8 8 8-8" fill="none" stroke="#23a3dd" stroke-width="2"/></svg></div>

<section>
  <h2 class="abs intro-title">DO YOU WANT TO SELL YOUR ENDOSCOPE?<br><span>YOU ARE AT THE RIGHT ADRESS!</span></h2>
  <div class="abs rule" style="left:566px;top:826px"></div>
  <svg class="abs" style="left:117px;top:866px" width="415" height="396" viewBox="0 0 415 396">
    <polygon points="105,2 310,2 412,200 310,358 105,358 3,200" fill="none" stroke="#23a3dd" stroke-width="2"/>
  </svg>
  <div class="abs" style="left:127px;top:877px;width:396px;height:340px;clip-path:polygon(25% 0,75% 0,100% 50%,75% 100%,25% 100%,0 50%);background:radial-gradient(circle at 45% 45%,#2b2f35 0%,#6b737c 40%,#d8dde2 75%)" role="img" aria-label="Photo of an endoscope control body with angulation knobs"></div>
  <div class="abs" style="left:338px;top:1105px;width:180px;height:155px;clip-path:polygon(25% 0,75% 0,100% 50%,75% 100%,25% 100%,0 50%);background:#fff"></div>
  <div class="abs" style="left:345px;top:1111px;width:168px;height:145px;clip-path:polygon(25% 0,75% 0,100% 50%,75% 100%,25% 100%,0 50%);background:radial-gradient(circle at 50% 60%,#1f2328,#7f878f 60%,#dfe3e7)" role="img" aria-label="Close-up photo of an endoscope connector"></div>
  <div class="abs intro-text">
    <p>We are always interested in buying used endoscopes, accessories and peripherals from Orvana, Pentrix and Fujiro at fair conditions. We can promise you an objective offer with a clear conscience! Use the form below to offer us your device! If you want to have several devices checked, one of our technicians will usually come to you for the check. We also check defective and incomplete devices!</p>
    <p>We would be happy to take a look at your device!</p>
  </div>
</section>

<section class="abs cta" role="img" aria-label="Dark blue tinted photo of endoscopes and cables on a workbench">
  <h2>ARE YOU LOOKING TO REPLACE YOUR<br>FOR SALE DEVICE?</h2>
  <div class="rule" style="position:absolute;left:563px;top:175px"></div>
  <p>Lorem ipsum dolor sit amet, consectetur adipiscing elit, sed do eiusmod tempor incididunt ut labore et dolore magna aliqua. Ut enim ad minim veniam.</p>
  <div class="btn">Browse our range of excellent used equipment!</div>
</section>

<div class="abs form-bg"></div>
<svg class="abs band" style="top:1748px" viewBox="0 0 1200 100" preserveAspectRatio="none">
  <polygon points="0,0 600,60 0,100" fill="#23a3dd"/>
  <polygon points="1200,0 600,60 1200,100" fill="#3f5c75"/>
</svg>
<div class="abs circle-arrow" style="left:578px;top:1776px;width:64px;height:64px"><svg width="20" height="24" viewBox="0 0 22 26"><path d="M11 2v21M3 15l8 8 8-8" fill="none" stroke="#23a3dd" stroke-width="2"/></svg></div>

<form>
  <h3 class="abs sec-h" style="left:136px;top:1914px">PERSONAL INFORMATION</h3>
  <label class="abs lbl" style="left:140px;top:1982px">Salutation *</label>
  <label class="abs lbl" style="left:359px;top:1982px">co. / dr. off. *</label>
  <div class="abs field" style="left:137px;top:2007px;width:207px;height:49px">Choose <svg width="14" height="9" viewBox="0 0 14 9"><path d="M1 1l6 6 6-6" fill="none" stroke="#1f3246" stroke-width="2"/></svg></div>
  <div class="abs field" style="left:355px;top:2007px;width:244px;height:49px">Company / doctor office</div>
  <label class="abs lbl" style="left:142px;top:2080px">Surname *</label>
  <label class="abs lbl" style="left:614px;top:2080px">First name*</label>
  <div class="abs field" style="left:140px;top:2109px;width:458px;height:49px"></div>
  <div class="abs field" style="left:613px;top:2109px;width:458px;height:49px"></div>
  <label class="abs lbl" style="left:142px;top:2178px">Email *</label>
  <label class="abs lbl" style="left:614px;top:2178px">Telephone*</label>
  <div class="abs field" style="left:140px;top:2206px;width:458px;height:49px"></div>
  <div class="abs field" style="left:613px;top:2206px;width:458px;height:49px"></div>

  <h3 class="abs sec-h" style="left:138px;top:2315px">INFORMATIONS ABOUT THE DEVICE</h3>
  <label class="abs lbl" style="left:138px;top:2378px">Brand *</label>
  <label class="abs lbl" style="left:356px;top:2378px">Model*</label>
  <label class="abs lbl" style="left:611px;top:2375px">Defects / damage</label>
  <div class="abs field" style="left:134px;top:2403px;width:208px;height:49px">Choose <svg width="14" height="9" viewBox="0 0 14 9"><path d="M1 1l6 6 6-6" fill="none" stroke="#1f3246" stroke-width="2"/></svg></div>
  <div class="abs field" style="left:353px;top:2403px;width:244px;height:49px">Choose <svg width="14" height="9" viewBox="0 0 14 9"><path d="M1 1l6 6 6-6" fill="none" stroke="#1f3246" stroke-width="2"/></svg></div>
  <div class="abs field" style="left:609px;top:2403px;width:458px;height:139px"></div>
  <label class="abs lbl" style="left:136px;top:2466px">Asking Price *</label>
  <div class="abs field" style="left:134px;top:2494px;width:459px;height:48px"></div>

  <h3 class="abs sec-h" style="left:133px;top:2588px">REMARKS AND PICTURE</h3>
  <label class="abs lbl" style="left:133px;top:2638px">Remarks and picture</label>
  <label class="abs lbl" style="left:618px;top:2642px">Upload picture</label>
  <div class="abs field top" style="left:130px;top:2666px;width:459px;height:76px">Description of the error, other information etc</div>
  <div class="abs field" style="left:618px;top:2666px;width:457px;height:76px;color:#8693a0">Drag &amp; drop you picture here or
    <span class="browse"><svg width="14" height="13" viewBox="0 0 14 13"><path d="M7 9V1M3.5 4.5 7 1l3.5 3.5M1 8v4h12V8" fill="none" stroke="#23a3dd" stroke-width="1.5"/></svg>Browse</span></div>
  <p class="abs note" style="left:623px;top:2748px">allowed formats: jpg, jpeg, png or bmp<br>maximum file size: 4 MB</p>

  <div class="abs check"></div>
  <p class="abs consent">I have read the privacy policy and accept it. I agree above input will be transmitted to Lumavex GmbH to get in contact with me respectively to process my request and store all needed informations. Neither a transfer to third parties will happen, nor a use for advertising purposes by Lumavex GmbH!</p>
  <div class="abs send">SEND</div>
</form>

<svg class="abs band" style="top:2984px;height:106px" viewBox="0 0 1200 106" preserveAspectRatio="none">
  <polygon points="0,106 1200,106 1200,100 600,60 0,106" fill="#fff"/>
  <polygon points="0,0 600,60 0,106" fill="#23a3dd"/>
  <polygon points="1200,0 600,60 1200,100" fill="#12293f"/>
</svg>
<div class="abs circle-arrow" style="left:581px;top:3013px;width:60px;height:60px"><svg width="18" height="22" viewBox="0 0 22 26"><path d="M11 24V3M3 11l8-8 8 8" fill="none" stroke="#23a3dd" stroke-width="2"/></svg></div>

<footer>
  <div class="abs footer"></div>
  <div class="abs f-brand"><i></i>Lumavex</div>
  <p class="abs f-about">Lorem ipsum dolor sit amet, consectetur adipiscing elit, sed do eiusmod tempor incididunt ut labore et dolore</p>
  <div class="abs vsep" style="left:467px"></div>
  <div class="abs vsep" style="left:708px"></div>
  <div class="abs vsep" style="left:913px"></div>
  <div class="abs f-col" style="left:467px"><h4>NAVIGATION</h4></div>
  <div class="abs f-links" style="left:488px;top:3163px">Home<br>Endoscope Repair<br>Used Endoscope<br>Endoscopy Systems</div>
  <div class="abs f-col" style="left:708px"><h4>RESOURCES</h4></div>
  <div class="abs f-links" style="left:723px;top:3163px">Endoscopy Accesories<br>Purchase<br>Contact Us</div>
  <div class="abs f-col" style="left:913px"><h4>FOLLOW US</h4></div>
  <div class="abs social"><span></span><span></span><span></span><span></span></div>
  <div class="abs f-rule"></div>
  <p class="abs copy">© 2022 Lumavex GmbH</p>
</footer>

</body>
</html>
```